Sparrow Haulage needs a business card design.

Design a double-sided business card for new freight business. On the front, would like to see our logo along with the following info:

Martin Obuya
CEO/FOUNDER
555-206-7142
martinobuya@sparrow-haulage.example

On the reverse side, we would like to use the graphic image of our logo only without the Sparrow Haulage name.

```html
<!DOCTYPE html>
<html lang="en">
<head>
<meta charset="utf-8">
<title>Sparrow Haulage — Business Card</title>
<link href="https://fonts.googleapis.com/css2?family=Michroma&family=Arimo:wght@400;700&display=swap" rel="stylesheet">
<style>
  :root {
    --navy: #0a0a6b;
    --red: #b00a0f;
    --white: #ffffff;
    --stage: #2b2b2b;
  }
  html, body {
    margin: 0;
    padding: 0;
    width: 1200px;
    height: 1015px;
    overflow: hidden;
    background: var(--stage);
  }
  .canvas {
    position: relative;
    width: 1200px;
    height: 1015px;
  }
  .card {
    position: absolute;
    left: 232px;
    width: 735px;
    height: 420px;
    overflow: hidden;
    box-shadow: 0 12px 30px rgba(0,0,0,0.55);
  }
  .card--back {
    top: 60px;
    background: var(--navy);
    display: flex;
    align-items: center;
    justify-content: center;
  }
  .back-mark {
    width: 96px;
    height: 96px;
    border-radius: 50%;
    background: var(--red);
  }
  .card--front {
    top: 535px;
    background: var(--white);
  }
  .wave {
    position: absolute;
    inset: 0;
    width: 100%;
    height: 100%;
  }
  .brand {
    position: absolute;
    left: 48px;
    top: 88px;
    display: flex;
    align-items: center;
    gap: 16px;
  }
  .brand__dot {
    width: 22px;
    height: 22px;
    border-radius: 50%;
    background: var(--red);
    flex: none;
  }
  .brand__name {
    font-family: "Michroma", sans-serif;
    font-size: 28px;
    letter-spacing: 3px;
    line-height: 1.15;
    text-transform: uppercase;
    color: var(--navy);
  }
  .contact {
    position: absolute;
    right: 36px;
    top: 196px;
    text-align: right;
    color: var(--white);
    font-family: "Arimo", sans-serif;
  }
  .contact__name {
    margin: 0;
    font-size: 27px;
    font-weight: 700;
    letter-spacing: 0.5px;
    text-transform: uppercase;
  }
  .contact__title {
    margin: 2px 0 14px;
    font-size: 20px;
    text-transform: uppercase;
  }
  .contact__list {
    list-style: none;
    margin: 0;
    padding: 0;
    font-size: 17px;
    line-height: 1.5;
  }
  .contact__list li {
    display: flex;
    align-items: center;
    justify-content: flex-end;
    gap: 8px;
  }
  .contact__icon { width: 15px; height: 15px; flex: none; }
</style>
</head>
<body>
<main class="canvas">

  <section class="card card--back" aria-label="Card reverse">
    <div class="back-mark" role="img" aria-label="Sparrow Haulage logo symbol"></div>
  </section>

  <section class="card card--front" aria-label="Card front">
    <svg class="wave" viewBox="0 0 735 420" preserveAspectRatio="none" aria-hidden="true">
      <path d="M0,420 L0,392 C210,392 310,330 430,195 C510,110 610,92 735,84 L735,420 Z" fill="var(--navy)"/>
      <path d="M0,378 C205,378 300,318 418,185 C498,98 600,76 720,68" fill="none" stroke="var(--red)" stroke-width="9"/>
      <path d="M0,388 C208,388 306,326 425,191" fill="none" stroke="var(--white)" stroke-width="4"/>
    </svg>

    <div class="brand">
      <span class="brand__dot"></span>
      <span class="brand__name">Sparrow<br>Haulage</span>
    </div>

    <div class="contact">
      <p class="contact__name">Martin Obuya</p>
      <p class="contact__title">CEO/Founder</p>
      <ul class="contact__list">
        <li>555-206-7142
          <svg class="contact__icon" viewBox="0 0 16 16"><path d="M3 1.5l3 .5 1 3.5-2 1.3a9 9 0 0 0 4.2 4.2l1.3-2 3.5 1 .5 3-2 1.5C6.5 14 2 9.5 1.5 3.5z" fill="var(--white)"/></svg>
        </li>
        <li>martinobuya@sparrow-haulage.example
          <svg class="contact__icon" viewBox="0 0 16 16"><rect x="1" y="3" width="14" height="10" fill="var(--white)"/><path d="M1 3l7 6 7-6" fill="none" stroke="var(--navy)" stroke-width="1.4"/></svg>
        </li>
        <li>www.sparrow-haulage.example
          <svg class="contact__icon" viewBox="0 0 16 16"><circle cx="8" cy="8" r="7" fill="var(--white)"/><path d="M1 8h14M8 1v14M8 1c-4 4-4 10 0 14M8 1c4 4 4 10 0 14" fill="none" stroke="var(--navy)" stroke-width="1"/></svg>
        </li>
      </ul>
    </div>
  </section>

</main>
</body>
</html>
```